Business Card Design

New business card design

Target Market(s)

Residential & Commercial Property Managers

Industry/Entity Type

Plumbing Services

Contact Information for Business Card

Name - Rowan Keddle, title - Director, Phone Number - 0431 286 517, email - rowan@tbk-plumbing.com.au, Company ABN - 73 215 904 386,

Font styles to use
Sans Serif

Colors
0054AA
0677BA
7BADD7
CADEEF
E8F1F8

```html
<!DOCTYPE html>
<html lang="en">
<head>
<meta charset="utf-8">
<title>TBK Plumbing Services – Business Card</title>
<link href="https://fonts.googleapis.com/css2?family=Questrial&family=Roboto:wght@400&display=swap" rel="stylesheet">
<style>
  :root {
    --stage: #c3c3c3;
    --card-light: #ffffff;
    --card-dark: #1d232a;
    --brand-blue: #00aeef;
    --ink: #1d232a;
    --text-grey: #444a50;
    --tagline-grey: #6b6b6b;
    --white: #ffffff;
  }
  * { box-sizing: border-box; margin: 0; padding: 0; }
  html, body {
    width: 1093px;
    height: 1200px;
    overflow: hidden;
    background: var(--stage);
  }
  .card {
    position: absolute;
    left: 265px;
    width: 580px;
    height: 356px;
    border-radius: 30px;
    overflow: hidden;
  }
  .card--front { top: 226px; background: var(--card-light); }
  .card--back  { top: 621px; background: var(--card-dark); }

  .wordmark {
    position: absolute;
    font-family: "Questrial", sans-serif;
    font-weight: 400;
    line-height: 1;
    letter-spacing: 0.04em;
  }
  .tagline {
    position: absolute;
    font-family: "Questrial", sans-serif;
    font-weight: 400;
    text-transform: lowercase;
    white-space: nowrap;
  }

  /* Front */
  .card--front .wordmark {
    left: 24px; top: 30px;
    font-size: 62px;
    color: var(--ink);
  }
  .card--front .tagline {
    left: 36px; top: 106px;
    font-size: 10px;
    letter-spacing: 0.98em;
    color: var(--tagline-grey);
  }
  .name-marker {
    position: absolute;
    left: -18px; top: 167px;
    width: 36px; height: 36px;
    border-radius: 50%;
    background: var(--brand-blue);
  }
  .person-name {
    position: absolute;
    left: 25px; top: 162px;
    font-family: "Questrial", sans-serif;
    font-size: 25px;
    letter-spacing: 0.03em;
    color: var(--ink);
  }
  .person-title {
    position: absolute;
    left: 25px; top: 191px;
    font-family: "Roboto", sans-serif;
    font-size: 17px;
    color: var(--brand-blue);
  }
  .contact-list {
    position: absolute;
    left: 26px; top: 238px;
    list-style: none;
    font-family: "Roboto", sans-serif;
    font-size: 17px;
    color: var(--text-grey);
  }
  .contact-list li {
    display: flex;
    align-items: center;
    gap: 6px;
    height: 21px;
  }
  .contact-list svg { width: 17px; height: 17px; fill: var(--brand-blue); }
  .abn {
    position: absolute;
    left: 26px; top: 295px;
    font-family: "Roboto", sans-serif;
    font-size: 17px;
    color: var(--text-grey);
  }
  .abn__label { color: var(--brand-blue); }
  .accent-disc {
    position: absolute;
    left: 324px; top: 98px;
    width: 254px; height: 254px;
    border-radius: 50%;
    background: var(--brand-blue);
  }

  /* Back */
  .card--back .wordmark {
    left: 0; right: 0; top: 100px;
    text-align: center;
    font-size: 100px;
    color: var(--white);
  }
  .card--back .tagline {
    left: 0; right: 0; top: 220px;
    text-align: center;
    font-size: 14px;
    letter-spacing: 1.1em;
    padding-left: 1.1em;
    color: var(--white);
  }
</style>
</head>
<body>

<section class="card card--front" aria-label="Business card front">
  <div class="wordmark">tbk</div>
  <div class="tagline">plumbing services</div>

  <span class="name-marker"></span>
  <h1 class="person-name">Rowan Keddle</h1>
  <p class="person-title">Director</p>

  <ul class="contact-list">
    <li>
      <svg viewBox="0 0 24 24" aria-hidden="true"><path d="M6.6 10.8a15.1 15.1 0 0 0 6.6 6.6l2.2-2.2a1 1 0 0 1 1-.25 11.4 11.4 0 0 0 3.6.57 1 1 0 0 1 1 1V20a1 1 0 0 1-1 1A17 17 0 0 1 3 4a1 1 0 0 1 1-1h3.5a1 1 0 0 1 1 1c0 1.25.2 2.45.57 3.57a1 1 0 0 1-.25 1z"/></svg>
      <span>0431 286 517</span>
    </li>
    <li>
      <svg viewBox="0 0 24 24" aria-hidden="true"><path d="M2 5h20v14H2z M2 5l10 8 10-8" fill="var(--brand-blue)"/><path d="M2 5l10 8 10-8" fill="none" stroke="#fff" stroke-width="1.5"/></svg>
      <span>rowan@tbk-plumbing.com.au</span>
    </li>
  </ul>

  <p class="abn"><span class="abn__label">Company ABN</span> - 73 215 904 386</p>

  <div class="accent-disc" role="img" aria-label="Large blue decorative accent shape"></div>
</section>

<section class="card card--back" aria-label="Business card back">
  <div class="wordmark">tbk</div>
  <div class="tagline">plumbing services</div>
</section>

</body>
</html>
```